Veltrane Group Business Card Design

The CEO is looking for a new trendy look for his business card.
You can stay with current branding or come up with something new/creative. It can be 3D, including Medical Office buildings. You can use our logo in a variety of colors. Please include name, title, company name, company website, email address, cell number

Target Market(s)

Real Estate Development and Construction

Industry/Entity Type

Health care real estate

Contact Information for Business Card

Rohesh Kamdar, CEO M-604.781.2249 E-roheshkamdar@veltrane.com Address:4180 Lindqvist Ave, Tampa, FL 33482 www.veltrane.com

Font styles to use
Other font styles liked:
• Be creative

Requirements
Must have
• Creative, trendy look
Nice to have
• Please go to our website to get a feel- www. veltrane.com
Should not have
• small fonts

```html
<!DOCTYPE html>
<html lang="en">
<head>
<meta charset="utf-8">
<title>Veltrane Group – Business Card</title>
<link rel="stylesheet" href="https://fonts.googleapis.com/css2?family=Montserrat:wght@400;500;700;800&display=swap">
<style>
  :root {
    --bg: #dcdcd9;
    --card-white: #ffffff;
    --card-black: #171717;
    --brand-red: #b11e28;
    --name-red: #d6322f;
    --brand-navy: #1c3155;
    --text-light: #f2f2f2;
    --logo-silver: #bdbdbd;
  }
  * { box-sizing: border-box; margin: 0; padding: 0; }
  html, body {
    width: 1200px; height: 801px; overflow: hidden;
    background: var(--bg);
    font-family: "Montserrat", Arial, sans-serif;
  }
  .stage {
    position: relative; width: 1200px; height: 801px;
    display: flex; align-items: center; justify-content: center; gap: 40px;
  }
  .card {
    position: relative; width: 540px; height: 309px; overflow: hidden;
    border-bottom: 3px solid var(--brand-red);
    box-shadow: 0 10px 24px rgba(0,0,0,.18);
  }
  .card--front { background: var(--card-white); }
  .card--back { background: var(--card-black); display: flex; align-items: center; justify-content: center; }

  .card__wave { position: absolute; inset: 0; width: 100%; height: 100%; }

  .brand-name {
    position: absolute; right: 26px; top: 26px;
    font-weight: 800; font-size: 38px; letter-spacing: -1px; line-height: 1;
    color: var(--brand-red); white-space: nowrap;
  }
  .brand-name--back {
    position: static; font-size: 56px; color: var(--logo-silver);
  }

  .contact { position: absolute; left: 34px; top: 130px; color: var(--text-light); }
  .contact__marker {
    position: absolute; left: -34px; top: 2px; width: 16px; height: 24px;
    background: var(--brand-red);
  }
  .contact__name {
    font-weight: 700; font-size: 19px; color: var(--name-red);
    text-transform: uppercase; letter-spacing: .5px; line-height: 1.1;
  }
  .contact__title { font-size: 12px; font-weight: 500; margin-top: 3px; }
  .contact__address { font-size: 12px; line-height: 1.4; margin-top: 12px; }
  .contact__list { list-style: none; margin-top: 10px; font-size: 12px; line-height: 1.55; }
  .contact__list li { display: flex; align-items: center; gap: 8px; }
  .contact__icon { width: 11px; height: 11px; flex: none; }
</style>
</head>
<body>
<main class="stage">

  <section class="card card--front" aria-label="Business card front">
    <svg class="card__wave" viewBox="0 0 540 309" preserveAspectRatio="none" aria-hidden="true">
      <defs>
        <path id="swoosh" d="M0,40 C100,95 220,108 330,116 C430,124 500,170 540,232 L540,340 L0,340 Z"/>
      </defs>
      <use href="#swoosh" transform="translate(0,-20)" fill="var(--brand-red)"/>
      <use href="#swoosh" transform="translate(0,-14)" fill="var(--card-white)"/>
      <use href="#swoosh" transform="translate(0,-11)" fill="var(--brand-navy)"/>
      <use href="#swoosh" transform="translate(0,-3)" fill="var(--card-white)"/>
      <use href="#swoosh" fill="var(--card-black)"/>
    </svg>

    <div class="brand-name">Veltrane Group</div>

    <div class="contact">
      <span class="contact__marker"></span>
      <h1 class="contact__name">Rohesh Kamdar</h1>
      <p class="contact__title">CEO</p>
      <p class="contact__address">4180 Lindqvist Ave,<br>Tampa, FL 33482</p>
      <ul class="contact__list">
        <li>
          <svg class="contact__icon" viewBox="0 0 12 12" aria-hidden="true"><rect x="3" y="0.5" width="6" height="11" rx="1" fill="none" stroke="var(--name-red)" stroke-width="1.2"/><circle cx="6" cy="9.5" r=".7" fill="var(--name-red)"/></svg>
          604.781.2249
        </li>
        <li>
          <svg class="contact__icon" viewBox="0 0 12 12" aria-hidden="true"><rect x="0.5" y="2.5" width="11" height="7.5" fill="var(--name-red)"/><path d="M0.5,2.5 L6,7 L11.5,2.5" fill="none" stroke="var(--card-black)" stroke-width="1"/></svg>
          roheshkamdar@veltrane.com
        </li>
        <li>
          <svg class="contact__icon" viewBox="0 0 12 12" aria-hidden="true"><circle cx="6" cy="6" r="5.5" fill="var(--name-red)"/><path d="M0.5,6 H11.5 M6,0.5 C3,3 3,9 6,11.5 M6,0.5 C9,3 9,9 6,11.5" fill="none" stroke="var(--card-black)" stroke-width=".8"/></svg>
          www.veltrane.com
        </li>
      </ul>
    </div>
  </section>

  <section class="card card--back" aria-label="Business card back">
    <div class="brand-name brand-name--back">Veltrane Group</div>
  </section>

</main>
</body>
</html>
```